International oil and gas consultancy business needs a web design

Hello, I need a web design for a new oil and gas auditing consultancy business. My business undertakes contract audit assignments to review past costs of oil and gas operations (see attached Excel file for more details of the businesses services). I need the design to give the impression of a professional consultancy style of business, rather than a retail style of website. Note: this job is for LAYOUT DESIGN ONLY and not coding / development work.
The following are my key design principles:
1. BASIC DESIGN: I am after a simple and static web design. I don't want the pages busy or cluttered with too many images or detail.
2. HORIZONTAL TABS: I require a horizontal set of tabs towards the top of the screens (see Excel file) which remain in the same position on every page.
3. META TAG PLANNING: The design should allow for effective positioning of content so that key meta tag words can easily be built during the technical build stage.
4. NUMBER OF PAGES: The site will eventually have a maximum of 10 pages. Seven of the pages will reside under the tabs. Can you please present your opening submission for the first two page.
5. USE OF MY LOGO: The attached logo (JPEG file) should be used throughout the website. Please don't change the shape and colour.
6. COLOUR SCHEMES: Can you please consider any of the 3 colour schemes below:
A - dark red (to match the logo), light grey and perhaps another of your liking;
B - dark red (to match the logo), light cream and perhaps another of your liking;
C - dark red (to match the logo), white and perhaps another of your liking.
7. WORD CONTENT: I have attached an Excel file which shows the estimated word content for each page.
8. FUTURE USE OF DESIGN: I'm planning on building a Wordpress website. Can you please ensure the layout design supports this application.

Target Market(s)

oil and gas companies (small and large)

Industry/Entity Type

Oil And Gas

Font styles to use
Sans Serif

Requirements
Nice to have
• The KRL logo and business name should ideally be next to each other. Also, the logo and name should be part of the background graphics, not above it.

```html
<!DOCTYPE html>
<html lang="en">
<head>
<meta charset="utf-8">
<title>KRL – Kestrel Review Limited</title>
<link href="https://fonts.googleapis.com/css2?family=Open+Sans:wght@400;600;700&display=swap" rel="stylesheet">
<style>
:root{
  --brand-red:#9b1b1f;
  --text-grey:#8a8a8a;
  --dark:#111;
  --nav-top:#3a3a3a;
  --nav-bottom:#0c0c0c;
  --white:#fff;
}
*{box-sizing:border-box;margin:0;padding:0}
html,body{width:1200px;height:1129px;overflow:hidden;background:var(--white);font-family:"Open Sans",sans-serif}
.page{position:relative;width:1200px;height:1129px}

.site-header{position:absolute;left:0;top:0;width:1200px;height:107px}
.brand{position:absolute;left:180px;top:6px;color:var(--brand-red);font-weight:700}
.brand-mark{display:flex;align-items:center;gap:10px;font-size:54px;line-height:64px;letter-spacing:2px}
.brand-mark .dot{width:14px;height:14px;background:var(--brand-red)}
.brand-name{font-size:15px;letter-spacing:1.5px;margin-top:4px}

.social{position:absolute;top:45px;left:838px;display:flex;gap:18px}
.social span{width:32px;height:32px;border-radius:3px;display:block}
.social .feed{background:linear-gradient(#fbd24a,#f0a516)}
.social .bird{background:linear-gradient(#8fd6f3,#48b2e0)}
.social .ball{background:linear-gradient(#f3a7c6,#d9679a)}
.social .book{background:linear-gradient(#4f7fd0,#2b56a6)}

.main-nav{position:absolute;left:0;top:107px;width:1200px;height:38px;background:linear-gradient(var(--nav-top),var(--nav-bottom));border-top:1px solid #000}
.main-nav ul{list-style:none;display:flex;margin-left:177px;height:100%}
.main-nav li{color:var(--white);font-size:11px;line-height:37px;padding:0 18px;border-right:1px solid #555}
.main-nav li:last-child{border-right:none}

.hero{position:absolute;left:0;top:145px;width:1200px;height:485px;background:linear-gradient(120deg,#efe7e0 0%,#dfe3ea 45%,#b8c6da 60%,#eef0f3 80%,#dcdcdc 100%)}
.hero-caption{position:absolute;left:204px;top:137px;width:426px;height:156px;background:rgba(255,255,255,.78);padding:24px 14px 0 15px}
.hero-caption h1{font-size:15.5px;font-weight:600;color:var(--brand-red);margin-bottom:12px}
.hero-caption p{font-size:12px;line-height:17px;color:#777}
.slider-dots{position:absolute;left:579px;top:450px;display:flex;gap:8px}
.slider-dots span{width:9px;height:9px;border-radius:50%;background:#999}
.slider-dots span:first-child{background:var(--white)}

.services-title{position:absolute;left:181px;top:660px;font-size:16.5px;font-weight:600;color:var(--brand-red)}
.service{position:absolute;top:708px;width:268px}
.service .thumb{height:138px}
.service h2{font-size:12px;font-weight:600;color:var(--brand-red);margin:26px 0 18px 1px}
.service:first-of-type h2{margin-top:21px}
.service p{font-size:11px;line-height:17px;color:var(--text-grey)}
.btn{position:absolute;top:266px;left:0;width:75px;height:26px;border-radius:3px;background:linear-gradient(#333,#000);color:var(--white);font-size:11px;line-height:26px;text-align:center}
.s1{left:180px}.s2{left:466px}.s3{left:752px}
.s1 .thumb{background:linear-gradient(135deg,#e6ecf3,#9fb2c8 60%,#2b3140)}
.s2 .thumb{background:linear-gradient(135deg,#dfe3e8,#f2f2f2 50%,#3a62a8)}
.s3 .thumb{background:linear-gradient(90deg,#2f3a50,#e5b9a3 45%,#d7a58d 65%,#3a4458)}

.site-footer{position:absolute;left:0;top:1041px;width:1200px;height:88px;background:linear-gradient(#444,#0a0a0a);color:var(--white);text-align:center}
.footer-links{margin-top:27px;font-size:11px;word-spacing:2px}
.footer-links .sep{margin:0 6px}
.copyright{font-size:11px;margin-top:5px}
</style>
</head>
<body>
<div class="page">
  <header class="site-header">
    <div class="brand">
      <div class="brand-mark"><span>KRL</span><span class="dot"></span></div>
      <div class="brand-name">Kestrel Review Limited</div>
    </div>
    <div class="social">
      <span class="feed" role="img" aria-label="News feed"></span>
      <span class="bird" role="img" aria-label="Social profile"></span>
      <span class="ball" role="img" aria-label="Portfolio profile"></span>
      <span class="book" role="img" aria-label="Community page"></span>
    </div>
  </header>

  <nav class="main-nav">
    <ul>
      <li>HOME</li><li>ABOUT US</li><li>SERVICES</li><li>OUR PARTNERS</li><li>APPROACH</li><li>WHY CHOOSE US</li><li>CONTACT US</li>
    </ul>
  </nav>

  <section class="hero" role="img" aria-label="Photo of business people reviewing charts on a tablet and printed reports">
    <div class="hero-caption">
      <h1>KESTREL REVIEW LIMITED</h1>
      <p>&nbsp;is a Perth (Australia) based firm specialising in providing quality audit services for the oil and gas industry. Our skills and knowledge of oil and gas, along with a deep understanding of business commercial needs, ensures the high quality of our services</p>
    </div>
    <div class="slider-dots"><span></span><span></span><span></span></div>
  </section>

  <h2 class="services-title">Kestrel Review Limited specialise in the following services</h2>

  <article class="service s1">
    <div class="thumb" role="img" aria-label="Photo of a hand using a tablet over financial charts"></div>
    <h2>JOIN VENTURE AUDITS</h2>
    <p>Sed ut perspiciatis unde omnis iste natus error sit voluptatem accusantium doloremque laudantium, totam rem aperiam,</p>
    <div class="btn">Read More</div>
  </article>
  <article class="service s2">
    <div class="thumb" role="img" aria-label="Photo of a meeting discussing printed bar charts"></div>
    <h2>CONTRACT AUDITS</h2>
    <p>Sed ut perspiciatis unde omnis iste natus error sit voluptatem accusantium doloremque laudantium, totam rem aperiam,</p>
    <div class="btn">Read More</div>
  </article>
  <article class="service s3">
    <div class="thumb" role="img" aria-label="Photo of a business handshake"></div>
    <h2>OPERATION AUIDITS</h2>
    <p>Sed ut perspiciatis unde omnis iste natus error sit voluptatem accusantium doloremque laudantium, totam rem aperiam,</p>
    <div class="btn">Read More</div>
  </article>

  <footer class="site-footer">
    <div class="footer-links">Home<span class="sep">/</span>About us<span class="sep">/</span>Service<span class="sep">/</span>Our Partners<span class="sep">/</span>Approach<span class="sep">/</span>Why Choose us<span class="sep">/</span>Contact us</div>
    <div class="copyright">© copyright 2014 KRL. All right reserved.</div>
  </footer>
</div>
</body>
</html>
```